Create a business promotion flyer to leave in customer mailboxes. We are a bulk petroleum supplier, servicing any industry that requires diesel. Base in griffith NSW, servicing griffith area and surrounds.

Business Name - Terra Diesel
Fuel@terradiesel-example.com.au
Owen - 0491 570 362 ohartley@terradiesel-example.com.au
Liam - 0491 570 718 lprosser@terradiesel-example.com.au
Simon - 0491 570 905 skenway@terradiesel-example.com.au
Office 02 5550 1734

Bulk Fuel deliveries.
Oils & lubricants
Local Family owned business

```html
<!DOCTYPE html>
<html lang="en">
<head>
<meta charset="utf-8">
<title>Terra Diesel – Bulk Petroleum Supplier</title>
<link href="https://fonts.googleapis.com/css2?family=Barlow+Semi+Condensed:ital,wght@1,900&family=Oswald:wght@500;600&family=Montserrat:wght@600;700&display=swap" rel="stylesheet">
<style>
  :root{
    --red:#e8291c;
    --grey:#666666;
    --black:#0b0b0b;
    --white:#ffffff;
    --sky-top:#3f78b8;
    --sky-mid:#a9c6e6;
    --concrete:#cfc9c2;
  }
  *{margin:0;padding:0;box-sizing:border-box}
  html,body{width:861px;height:1200px;overflow:hidden;background:var(--white)}
  .flyer{position:relative;width:861px;height:1200px;background:var(--white);overflow:hidden;font-family:"Oswald",sans-serif}

  .brand-rule{position:absolute;height:6px}
  .brand-rule.grey{background:var(--grey)}
  .brand-rule.red{background:var(--red)}
  .brand{position:absolute;left:316px;width:229px;top:58px;height:44px;display:flex;align-items:center;justify-content:center;gap:7px}
  .brand-mark{width:14px;height:14px;background:var(--red);flex:none}
  .brand-name{font-family:"Montserrat",sans-serif;font-weight:600;font-size:25px;color:var(--red);white-space:nowrap}

  .hero-photo{position:absolute;left:0;top:221px;width:861px;height:620px;
    background:linear-gradient(180deg,var(--sky-top) 0%,var(--sky-mid) 28%,#e9eef3 45%,var(--concrete) 62%,#d8d3cd 82%,var(--white) 100%)}

  .headline{position:absolute;left:0;width:861px;text-align:center;font-family:"Barlow Semi Condensed",sans-serif;font-style:italic;font-weight:900;text-transform:uppercase;line-height:1;white-space:nowrap}
  .headline.lead{top:134px;font-size:64px;letter-spacing:2px;color:var(--black)}
  .headline.main{top:188px;font-size:80px;letter-spacing:1.5px;color:var(--red);text-shadow:3px 3px 0 #3a0b07}

  .tagline{position:absolute;left:0;width:861px;text-align:center;font-weight:600;font-size:56px;line-height:1;white-space:nowrap}
  .tagline.dark{top:594px;color:var(--black)}
  .tagline.red{top:660px;color:var(--red)}

  .services-title{position:absolute;top:814px;left:322px;width:186px;text-align:center;font-weight:600;font-size:44px;color:var(--black);line-height:1}
  .services-rule{position:absolute;top:839px;width:118px;height:3px;background:var(--red)}

  .service{position:absolute;display:flex;align-items:center;height:73px}
  .service-icon{width:87px;height:73px;display:flex;align-items:center;justify-content:center;flex:none}
  .service-icon.grey{background:var(--grey)}
  .service-icon.red{background:var(--red)}
  .service-label{margin-left:24px;font-weight:500;font-size:30px;line-height:1.05;color:var(--black);white-space:nowrap}

  .footer-shapes{position:absolute;left:0;top:1065px}
  .contact-title{position:absolute;left:35px;top:1106px;font-weight:500;font-size:30px;color:var(--red);line-height:1}
  .contact-email{position:absolute;left:35px;top:1150px;display:flex;align-items:center;gap:10px;font-family:"Montserrat",sans-serif;font-weight:600;font-size:16px;color:var(--white);white-space:nowrap}
  .phone-icon{position:absolute;left:474px;top:1101px}
  .phone-list{position:absolute;left:508px;top:1097px;list-style:none;font-family:"Montserrat",sans-serif;font-weight:700;font-size:24px;letter-spacing:1.2px;color:var(--white);line-height:30px;white-space:nowrap}
</style>
</head>
<body>
<div class="flyer">

  <div class="brand-rule grey" style="left:107px;top:57px;width:207px"></div>
  <div class="brand-rule red" style="left:65px;top:71px;width:249px"></div>
  <div class="brand-rule grey" style="left:30px;top:85px;width:284px"></div>

  <div class="brand-rule grey" style="left:547px;top:57px;width:207px"></div>
  <div class="brand-rule red" style="left:547px;top:71px;width:248px"></div>
  <div class="brand-rule grey" style="left:547px;top:85px;width:284px"></div>

  <div class="brand">
    <span class="brand-mark"></span>
    <span class="brand-name">Terra Diesel</span>
  </div>

  <div class="hero-photo" role="img" aria-label="Photo of a white road-train fuel tanker parked in front of a large steel depot shed under a blue cloudy sky, on a concrete yard"></div>

  <h1 class="headline lead">We are a bulk</h1>
  <h2 class="headline main">Petroleum Supplier</h2>

  <p class="tagline dark">Servicing Any Industry</p>
  <p class="tagline red">That Requires Diesel</p>

  <div class="services-rule" style="left:196px"></div>
  <h3 class="services-title">SERVICES</h3>
  <div class="services-rule" style="left:517px"></div>

  <div class="service" style="left:65px;top:889px">
    <div class="service-icon grey">
      <svg width="48" height="30" viewBox="0 0 48 30" fill="none" stroke="#fff" stroke-width="2.5">
        <rect x="2" y="5" width="28" height="14" rx="7"/><path d="M30 10h8l6 7v6H2"/><circle cx="10" cy="24" r="3.5" fill="#666"/><circle cx="36" cy="24" r="3.5" fill="#666"/>
      </svg>
    </div>
    <span class="service-label">Bulk Fuel Deliveries</span>
  </div>

  <div class="service" style="left:456px;top:889px">
    <div class="service-icon red">
      <svg width="48" height="32" viewBox="0 0 48 32" fill="none" stroke="#fff" stroke-width="2.5">
        <rect x="4" y="3" width="8" height="11"/><rect x="16" y="3" width="8" height="11"/><path d="M2 17h28v-7h8l7 8v7H2z"/><circle cx="11" cy="26" r="3.5" fill="#e8291c"/><circle cx="37" cy="26" r="3.5" fill="#e8291c"/>
      </svg>
    </div>
    <span class="service-label">Petrol Deliveries</span>
  </div>

  <div class="service" style="left:65px;top:975px">
    <div class="service-icon red">
      <svg width="36" height="40" viewBox="0 0 36 40" fill="none" stroke="#fff" stroke-width="2.8">
        <rect x="12" y="2" width="10" height="5"/><path d="M6 12l6-5h14v10"/><path d="M6 12v24h14"/><path d="M27 20c4 6 6 9 6 12a6 6 0 0 1-12 0c0-3 2-6 6-12z" fill="#fff"/>
      </svg>
    </div>
    <span class="service-label">Oils &amp; Lubricants</span>
  </div>

  <div class="service" style="left:456px;top:975px">
    <div class="service-icon grey">
      <svg width="44" height="42" viewBox="0 0 44 42" fill="#fff">
        <path d="M22 2l9 4v6c0 6-4 10-9 12-5-2-9-6-9-12V6z"/><path d="M18 13l3 3 6-6" fill="none" stroke="#666" stroke-width="2.5"/>
        <circle cx="8" cy="26" r="4"/><circle cx="36" cy="26" r="4"/><circle cx="22" cy="30" r="4"/>
        <path d="M1 40c0-5 3-8 7-8s7 3 7 8zM29 40c0-5 3-8 7-8s7 3 7 8zM15 42c0-5 3-7 7-7s7 2 7 7z"/>
      </svg>
    </div>
    <span class="service-label">Local Family Owned<br>Business</span>
  </div>

  <svg class="footer-shapes" width="861" height="135" viewBox="0 0 861 135">
    <polygon points="0,30 424,30 336,135 0,135" fill="#0b0b0b"/>
    <polygon points="461,0 861,0 861,135 342,135" fill="#e8291c"/>
  </svg>

  <p class="contact-title">Contact Us</p>
  <p class="contact-email">
    <svg width="17" height="12" viewBox="0 0 17 12"><rect width="17" height="12" fill="#e8291c"/><path d="M0 0l8.5 7L17 0" fill="none" stroke="#0b0b0b" stroke-width="1.5"/></svg>
    Fuel@terradiesel-example.com.au
  </p>

  <svg class="phone-icon" width="24" height="24" viewBox="0 0 24 24" fill="none" stroke="#fff" stroke-width="2.2" stroke-linecap="round">
    <path d="M5 3l4 1 1 5-2 2c1 2 3 4 5 5l2-2 5 1 1 4-3 3C10 21 3 14 2 6z"/><path d="M14 3a7 7 0 0 1 7 7M14 7a3 3 0 0 1 3 3"/>
  </svg>
  <ul class="phone-list">
    <li>Owen - 0491 570 362</li>
    <li>Liam - 0491 570 718</li>
    <li>Simon - 0491 570 905</li>
  </ul>

</div>
</body>
</html>
```